Business Cards for a law firm

Business cards for our law firm. Use our silhoette logo and OAK PARTNERS - check our website (www.oakpartners.example)

Contact Information for Business Card

our silhouette logo, OAK PARTNERS, 800-555-0147, Dorian Pemberton, dorian@oakpartners.example

Requirements
Must have
• our silhouette logo, OAK PARTNERS, 800-555-0147, Dorian Pemberton, dorian@oakpartners.example

```html
<!DOCTYPE html>
<html lang="en">
<head>
<meta charset="utf-8">
<title>Oak Partners – Business Cards</title>
<link href="https://fonts.googleapis.com/css2?family=Cinzel:wght@600&family=Montserrat:wght@400;700&display=swap" rel="stylesheet">
<style>
  :root {
    --navy: #233270;
    --navy-deep: #1d2a5e;
    --navy-light: #3a55a6;
    --ink: #2a2a2a;
    --paper: #ffffff;
    --backdrop: #e9e6e1;
  }
  * { margin: 0; padding: 0; box-sizing: border-box; }
  html, body { width: 900px; height: 1200px; overflow: hidden; }
  body {
    position: relative;
    background: var(--backdrop);
    font-family: "Montserrat", Arial, sans-serif;
  }
  .card {
    position: absolute;
    left: 80px;
    width: 742px;
    height: 440px;
    border-radius: 22px;
    overflow: hidden;
    box-shadow: 0 6px 14px rgba(0,0,0,0.25);
  }
  .card--front { top: 131px; background: var(--paper); }
  .card--back  { top: 638px; background: var(--navy); }

  .portrait-area {
    position: absolute;
    left: 8px; top: 32px;
    width: 272px; height: 404px;
    border-radius: 14px;
    background: linear-gradient(180deg, #2c3c80 0%, var(--navy) 100%);
  }
  .firm-name {
    position: absolute;
    left: 363px; top: 84px;
    font-family: "Cinzel", Georgia, serif;
    font-weight: 600;
    font-size: 27px;
    letter-spacing: 1.5px;
    color: var(--navy);
  }
  .person-name {
    position: absolute;
    left: 362px; top: 176px;
    font-weight: 700;
    font-size: 26px;
    color: var(--navy);
  }
  .person-role {
    position: absolute;
    left: 361px; top: 213px;
    font-size: 16px;
    color: var(--ink);
  }
  .address {
    position: absolute;
    left: 360px; top: 246px;
    font-size: 16px;
    line-height: 21px;
    color: var(--ink);
  }
  .contacts {
    position: absolute;
    left: 360px; top: 302px;
    list-style: none;
  }
  .contacts li {
    display: flex;
    align-items: center;
    height: 28px;
    font-size: 16px;
    color: var(--ink);
  }
  .contacts svg { width: 15px; height: 15px; margin-right: 9px; fill: var(--navy); }

  .pattern-area {
    position: absolute;
    inset: 0;
    background: linear-gradient(100deg, #3a58a8 0%, #2e4490 40%, var(--navy-deep) 75%, #1a2657 100%);
  }
  .back-mark {
    position: absolute;
    left: 226px; top: 288px;
    display: flex;
    align-items: center;
  }
  .back-mark .dot {
    width: 14px; height: 14px;
    border-radius: 50%;
    background: var(--paper);
    margin-right: 16px;
  }
  .back-mark .name {
    font-family: "Cinzel", Georgia, serif;
    font-weight: 600;
    font-size: 28px;
    letter-spacing: 1.5px;
    color: var(--paper);
  }
</style>
</head>
<body>
  <section class="card card--front">
    <div class="portrait-area" role="img" aria-label="Firm silhouette logo: two standing figures in suits"></div>
    <div class="firm-name">OAK PARTNERS</div>
    <div class="person-name">Dorian Pemberton</div>
    <div class="person-role">Lawyer</div>
    <div class="address">418 Linden Avenue, #112<br>Millbrook, OH 43999</div>
    <ul class="contacts">
      <li>
        <svg viewBox="0 0 16 16"><path d="M4 1l2.5 3-1.5 1.8c.9 1.9 2.4 3.4 4.2 4.2L11 8.5l3 2.5-1.5 3C7 14 2 9 2 3.5z"/></svg>
        800-555-0147
      </li>
      <li>
        <svg viewBox="0 0 16 16"><path d="M1 3h14v1.2L8 9 1 4.2z M1 5.8l7 4.8 7-4.8V13H1z"/></svg>
        dorian@oakpartners.example
      </li>
      <li>
        <svg viewBox="0 0 16 16"><circle cx="8" cy="8" r="7"/><path d="M3 6h10M3 10h10M8 1.5c-2.5 3-2.5 10 0 13M8 1.5c2.5 3 2.5 10 0 13" stroke="#fff" stroke-width="1" fill="none"/></svg>
        www.oakpartners.example
      </li>
    </ul>
  </section>

  <section class="card card--back">
    <div class="pattern-area" role="img" aria-label="Repeating pattern of the firm silhouette logo fading from light to dark blue"></div>
    <div class="back-mark">
      <span class="dot"></span>
      <span class="name">OAK PARTNERS</span>
    </div>
  </section>
</body>
</html>
```